Heron Haulage needs Bussiness cards!

Our new trucking company needs business cards!
We need the same design with two different names and emails, everything else it's the same.
I have included our original logo so we can use it for the design.
Note: the logo to be used is the o e with the buffalo on the right side, next to the letters H and H.

Target Market(s)

Trucking, refrigerated transportation, freight

Industry/Entity Type

Business

Contact Information for Business Card

Card #1:
Marcus Whitfield
marcuswhitfield@heronhaulage.example
1-855-317-6094
(956)238-7160
4117 W. Larkin Ave.
Pharr, TX 78590
www.heronhaulage.example

Card#2:
Rosalba Quintero
rosalba@heronhaulage.example
1-855-317-6094
(956)238-7160
4117 W. Larkin Ave.
Pharr, TX 78590
www.heronhaulage.example

Font styles to use
Sans Serif

Colors
0655a3
ec1f27
ffffff

Requirements
Must have
• our logo
Nice to have
• roads on background,

```html
<!DOCTYPE html>
<html lang="en">
<head>
<meta charset="utf-8">
<title>Heron Haulage – Business Cards</title>
<link rel="stylesheet" href="https://fonts.googleapis.com/css2?family=Open+Sans:wght@400;600;800&display=swap">
<style>
  :root {
    --navy: #0655a3;
    --navy-deep: #123a6b;
    --red: #ec1f27;
    --white: #ffffff;
    --ink: #333333;
    --divider: #b9dba6;
    --stage: #eeeeec;
    --sky: #9fb3c4;
    --field: #b98a4e;
    --road: #4a4a4a;
  }
  * { box-sizing: border-box; margin: 0; padding: 0; }
  html, body {
    width: 1200px; height: 900px; overflow: hidden;
    background: var(--stage);
    font-family: "Open Sans", Arial, sans-serif;
  }
  .sheet {
    width: 1200px; height: 900px;
    display: flex; flex-direction: column;
    align-items: center; justify-content: center; gap: 56px;
  }
  .card {
    position: relative;
    width: 620px; height: 354px;
    overflow: hidden;
    box-shadow: 0 6px 18px rgba(0,0,0,.18);
  }

  /* Front */
  .card--front { background: var(--road); }
  .card__photo {
    position: absolute; inset: 0;
    background: linear-gradient(180deg,
      #c9d3dc 0%, var(--sky) 18%, #8a8a7a 22%,
      var(--field) 30%, #a6773f 48%, #6d5a44 58%,
      var(--road) 66%, #3a3a3a 100%);
  }
  .card__brand-front {
    position: absolute; left: 60px; top: 150px;
    display: flex; align-items: center; gap: 14px;
    color: var(--white);
    font-weight: 800; font-size: 52px; letter-spacing: -1px;
  }
  .brand-dot { width: 26px; height: 26px; border-radius: 50%; background: currentColor; }

  /* Back */
  .card--back { background: var(--white); }
  .card__brand-back {
    position: absolute; top: 62px; left: 0; right: 0;
    display: flex; justify-content: center; align-items: center; gap: 12px;
    color: var(--navy);
    font-weight: 800; font-size: 44px; letter-spacing: -1px;
  }
  .card__brand-back .brand-dot { width: 22px; height: 22px; }
  .card__details {
    position: absolute; left: 0; right: 0; top: 212px;
    display: flex; justify-content: center;
  }
  .identity {
    text-align: right; padding-right: 16px; padding-top: 28px;
  }
  .identity__name { font-size: 19px; font-weight: 600; color: var(--red); }
  .identity__name .surname { color: var(--navy-deep); }
  .identity__address { font-size: 16px; color: var(--ink); margin-top: 6px; }
  .contacts {
    list-style: none;
    border-left: 1px solid var(--divider);
    padding-left: 12px;
    font-size: 12.5px; color: var(--ink); line-height: 20px;
  }
  .contacts li { display: flex; align-items: center; gap: 7px; }
  .contacts svg { width: 11px; height: 11px; fill: var(--red); flex: none; }
</style>
</head>
<body>
<main class="sheet">

  <section class="card card--front">
    <div class="card__photo" role="img" aria-label="Photograph of a straight highway running through golden prairie under a cloudy sky"></div>
    <div class="card__brand-front"><span class="brand-dot"></span>Heron Haulage</div>
  </section>

  <section class="card card--back">
    <div class="card__brand-back"><span class="brand-dot"></span>Heron Haulage</div>
    <div class="card__details">
      <div class="identity">
        <p class="identity__name">Marcus <span class="surname">Whitfield</span></p>
        <p class="identity__address">4117 W. Larkin Ave. Pharr, TX 78590</p>
      </div>
      <ul class="contacts">
        <li><svg viewBox="0 0 12 12"><path d="M3 0h6a1 1 0 0 1 1 1v10a1 1 0 0 1-1 1H3a1 1 0 0 1-1-1V1a1 1 0 0 1 1-1zm0 1.5v8h6v-8zM5.2 10.2h1.6v.8H5.2z"/></svg>1-855-317-6094</li>
        <li><svg viewBox="0 0 12 12"><path d="M1 4c0-2 2-3 5-3s5 1 5 3H8.5V3h-5v1zM2 5h8l1 6H1zm4 1.5a1.8 1.8 0 1 0 0 3.6 1.8 1.8 0 0 0 0-3.6z"/></svg>(956)238-7160</li>
        <li><svg viewBox="0 0 12 12"><path d="M0 2h12v1.2L6 7 0 3.2zm0 2.6 6 3.8 6-3.8V10H0z"/></svg>marcuswhitfield@heronhaulage.example</li>
        <li><svg viewBox="0 0 12 12"><circle cx="6" cy="6" r="6"/></svg>www.heronhaulage.example</li>
      </ul>
    </div>
  </section>

</main>
</body>
</html>
```